Sleek wordpress site for Bramblecrest finishing works

We are a commercial job shop that serves B2B, govt & LEO and retail clients.We need a wordpress site with 6 individual pages: homepage, coating, laser engraving, laser cutting, part marking, and contact us. I have attached an outline of the desired flow and sub headings for each page. I would like to incorporate the colors of the logo through out the site to be clean and sleek enough to appeal to B2B commercial clients yet be inviting enough for retail clients.

I would like to have easy picture functionality so photographs on each page can be updated easily.

Target Market(s)

B2B industrial & Govt and Military part marking, laser engraving and coating: machine shops, aerospace companies, tool manufactures. Retail: personalized gifts, Job Shop

Coding

Coded - Design and coding required

Font styles to use
Sans Serif
Other font styles liked:
• Open to suggestion

Colors
0255a3
3176b5
eaf1f7
cfdeed
ffffff

Requirements
Must have
• Clean easy to navigate flow, separate pages as indicated on attached outline, high class feel. Great picture functionality, professional and inviting feel,
• **update: needs to be optimized for mobile, should have a gallery function. Gallery can be an additional page or embedded
Nice to have
• Social media connectivity links,
Should not have
• crappy plugins that make back-end management difficult, no blog

```html
<!DOCTYPE html>
<html lang="en">
<head>
<meta charset="utf-8">
<title>Bramblecrest Finishing Works</title>
<link rel="stylesheet" href="https://fonts.googleapis.com/css2?family=Lato:ital,wght@0,400;0,700;1,700&family=Questrial&family=Exo+2:wght@800&family=Tinos:wght@700&display=swap">
<style>
:root{
  --brand:#0255a3;
  --brand-light:#3176b5;
  --tint:#eaf1f7;
  --tint-2:#cfdeed;
  --white:#ffffff;
  --ink:#555555;
  --muted:#777777;
  --band:#eeeeee;
}
*{box-sizing:border-box;margin:0;padding:0}
html,body{width:1009px;height:1200px;overflow:hidden;background:var(--white);font-family:'Lato',sans-serif;color:var(--ink)}
.page{position:relative;width:1009px;height:1200px}
.site-header{position:absolute;top:0;left:0;width:1009px;height:123px;border-top:4px solid var(--brand);background:var(--white);z-index:3}
.brand{position:absolute;left:0;top:0;width:255px;height:119px;display:flex;align-items:center;justify-content:center;gap:9px}
.brand-mark{width:14px;height:14px;border-radius:50%;background:var(--brand)}
.brand-name{font-family:'Lato',sans-serif;font-weight:700;font-size:14px;line-height:17px;color:var(--brand);letter-spacing:.5px}
.nav{position:absolute;left:255px;top:0;height:119px}
.nav a{position:absolute;top:0;height:119px;line-height:119px;font-family:'Questrial',sans-serif;font-size:15px;color:#666;text-decoration:none;white-space:nowrap}
.nav a.active{left:0;width:79px;background:var(--brand);color:var(--white);text-align:center}
.nav-tools{position:absolute;left:879px;top:48px;display:flex;gap:14px;align-items:center}
.cart{position:relative;display:flex}
.cart-count{position:absolute;top:-7px;right:-9px;width:16px;height:16px;border-radius:50%;background:var(--brand);color:var(--white);font-size:10px;font-weight:700;display:flex;align-items:center;justify-content:center;border:1.5px solid var(--white)}
.hero{position:absolute;top:123px;left:0;width:1009px;height:481px;background:radial-gradient(ellipse at 65% 30%,#8a8e96 0%,#5e636b 45%,#3f434a 100%)}
.hero-copy{position:absolute;top:148px;left:0;width:1009px;text-align:center;color:var(--white)}
.hero-title{font-family:'Exo 2',sans-serif;font-weight:800;font-size:41px;line-height:52px;text-shadow:0 2px 4px rgba(0,0,0,.45)}
.hero-text{font-family:'Lato',sans-serif;font-style:italic;font-weight:700;font-size:14px;line-height:23px;margin:12px auto 0;width:540px}
.hero-arrow{position:absolute;top:216px;width:44px;height:44px;border-radius:50%;background:var(--white);display:flex;align-items:center;justify-content:center}
.hero-arrow.prev{left:43px}.hero-arrow.next{left:922px}
.services{position:absolute;top:578px;left:66px}
.service{position:absolute;top:0;width:201px;height:228px;background:linear-gradient(180deg,var(--brand-light) 0%,var(--brand) 100%);text-align:center;color:var(--white);box-shadow:0 14px 12px -10px rgba(0,0,0,.35)}
.service-icon{position:absolute;left:56px;top:-44px;width:88px;height:88px;border-radius:50%;background:var(--white);border:4px solid var(--brand-light);display:flex;align-items:center;justify-content:center}
.service h3{font-family:'Questrial',sans-serif;font-weight:400;font-size:19px;margin-top:64px}
.service p{font-size:12.5px;line-height:21px;margin:9px 14px 0}
.btn{display:inline-block;margin-top:12px;width:105px;height:35px;line-height:35px;background:var(--white);color:#222;font-size:13.5px;text-decoration:none}
.welcome{position:absolute;top:853px;left:0;width:1009px;text-align:center}
.welcome h2{font-family:'Tinos',serif;font-weight:700;font-size:30px;color:var(--brand)}
.welcome h2 span{color:var(--brand-light)}
.welcome p{font-size:12.5px;line-height:21px;width:560px;margin:14px auto 0}
.contact-band{position:absolute;top:1007px;left:0;width:1009px;height:132px;background:var(--band)}
.contact-item{position:absolute;top:49px;display:flex;gap:14px;font-size:13.5px;line-height:21px;color:#666}
.contact-icon{width:44px;height:44px;border-radius:50%;background:var(--white);border:1px solid #ddd;display:flex;align-items:center;justify-content:center;flex-shrink:0}
.social{position:absolute;left:664px;top:49px;display:flex;gap:9px}
.social-link{width:35px;height:35px;border-radius:50%;border:1px solid #999;display:flex;align-items:center;justify-content:center}
.social-link.on{background:var(--brand);border-color:var(--brand)}
.site-footer{position:absolute;top:1139px;left:0;width:1009px;height:61px;background:var(--brand);color:var(--white);font-size:11px}
.copyright{position:absolute;left:70px;top:24px}
.copyright b{font-weight:700}
.footer-links{position:absolute;right:69px;top:24px}
.footer-links a{color:var(--white);text-decoration:none}
.footer-links i{font-style:normal;margin:0 7px;opacity:.8}
</style>
</head>
<body>
<div class="page">
  <header class="site-header">
    <div class="brand"><span class="brand-mark"></span><span class="brand-name">BRAMBLECREST<br>FINISHING WORKS</span></div>
    <nav class="nav">
      <a class="active" href="#">Home</a>
      <a href="#" style="left:104px">Coating</a>
      <a href="#" style="left:183px">Laser Engraving</a>
      <a href="#" style="left:315px">Lesar Cutting</a>
      <a href="#" style="left:428px">Part Marketing</a>
      <a href="#" style="left:552px">Contact</a>
    </nav>
    <div class="nav-tools">
      <svg width="20" height="20" viewBox="0 0 20 20" fill="none" stroke="#0255a3" stroke-width="1.6"><circle cx="8" cy="8" r="6.5"/><path d="M13 13l6 6"/></svg>
      <span class="cart"><svg width="22" height="20" viewBox="0 0 22 20" fill="#0255a3"><path d="M1 7h20l-2.5 11h-15z"/><path d="M5 7l5-6M17 7l-5-6" stroke="#0255a3" stroke-width="1.5" fill="none"/></svg><span class="cart-count">0</span></span>
    </div>
  </header>

  <section class="hero" role="img" aria-label="Technician operating a precision measuring machine in a workshop">
    <div class="hero-copy">
      <h1 class="hero-title">BRAMBLECREST FINISHING<br>WORKS</h1>
      <p class="hero-text">Lorem Ipsum is simply dummy text of the printing and typesetting industry. Lorem Ipsum has been the industry's standard dummy text ever since the 1500s.</p>
    </div>
    <span class="hero-arrow prev"><svg width="12" height="14" viewBox="0 0 12 14"><path d="M8 2L3 7l5 5" stroke="#222" stroke-width="2.2" fill="none"/></svg></span>
    <span class="hero-arrow next"><svg width="12" height="14" viewBox="0 0 12 14"><path d="M4 2l5 5-5 5" stroke="#0255a3" stroke-width="2.2" fill="none"/></svg></span>
  </section>

  <section class="services">
    <article class="service" style="left:0">
      <div class="service-icon"><svg width="44" height="44" viewBox="0 0 44 44" fill="#0255a3"><path d="M6 22L22 8l14 10-16 14z" fill="none" stroke="#0255a3" stroke-width="3"/><path d="M30 24c3 5 5 7 5 10a5 5 0 0 1-10 0c0-3 2-5 5-10z"/></svg></div>
      <h3>Coating</h3>
      <p>Lorem Ipsum is simply dummy of the printing and typesetting industry.</p>
      <a class="btn" href="#">READ MORE</a>
    </article>
    <article class="service" style="left:226px">
      <div class="service-icon"><svg width="44" height="44" viewBox="0 0 44 44" fill="#0255a3"><rect x="8" y="6" width="28" height="4"/><path d="M19 10h6l-3 6z"/><path d="M22 16v8" stroke="#0255a3" stroke-width="1.5"/><rect x="13" y="22" width="18" height="12"/><rect x="6" y="36" width="32" height="3"/></svg></div>
      <h3>Laser Engraving</h3>
      <p>Lorem Ipsum is simply dummy of the printing and typesetting industry.</p>
      <a class="btn" href="#">READ MORE</a>
    </article>
    <article class="service" style="left:452px">
      <div class="service-icon"><svg width="44" height="44" viewBox="0 0 44 44" fill="#0255a3"><rect x="18" y="4" width="8" height="14" rx="3"/><path d="M15 18h14l-3 6h-8z"/><path d="M22 24v8M14 30l8 2 8-2" stroke="#0255a3" stroke-width="1.5" fill="none"/><rect x="6" y="34" width="32" height="3"/></svg></div>
      <h3>Lesar Cutting</h3>
      <p>Lorem Ipsum is simply dummy of the printing and typesetting industry.</p>
      <a class="btn" href="#">READ MORE</a>
    </article>
    <article class="service" style="left:678px">
      <div class="service-icon"><svg width="44" height="44" viewBox="0 0 44 44" fill="none" stroke="#0255a3" stroke-width="2.5"><path d="M8 36L36 8M6 30l8 8M30 6l8 8"/><path d="M8 8l28 28M8 8l4-2 2 4"/></svg></div>
      <h3>Part Marketing</h3>
      <p>Lorem Ipsum is simply dummy of the printing and typesetting industry.</p>
      <a class="btn" href="#">READ MORE</a>
    </article>
  </section>

  <section class="welcome">
    <h2>Welcome to <span>Bramblecrest Finishing Works</span></h2>
    <p>Lorem Ipsum is simply dummy text of the printing and typesetting industry. Lorem Ipsum has been the industry's standard dummy text ever since the 1500s, when an unknown printer took a galley of type and scrambled it to make a type specimen book.</p>
  </section>

  <section class="contact-band">
    <div class="contact-item" style="left:64px">
      <span class="contact-icon"><svg width="20" height="18" viewBox="0 0 20 18" fill="#0255a3"><path d="M10 1L1 9h3v8h4v-5h4v5h4V9h3z"/></svg></span>
      <span>418 W Cedar Loop #7,<br>Tempe, AZ 85281</span>
    </div>
    <div class="contact-item" style="left:369px">
      <span class="contact-icon"><svg width="18" height="18" viewBox="0 0 18 18" fill="#0255a3"><path d="M3 1l4 1 1 4-2 2c1 2 3 4 5 5l2-2 4 1 1 4-3 2C8 17 1 10 1 4z"/></svg></span>
      <span>602.555.0148<br>hello@bramblecrestworks.com</span>
    </div>
    <div class="social" aria-label="Social media links">
      <a class="social-link on" href="#" aria-label="Share"><svg width="14" height="14" viewBox="0 0 14 14" fill="#fff" stroke="#fff" stroke-width="1.3"><circle cx="11" cy="3" r="2"/><circle cx="3" cy="7" r="2"/><circle cx="11" cy="11" r="2"/><path d="M3 7l8-4M3 7l8 4" fill="none"/></svg></a>
      <a class="social-link" href="#" aria-label="Website"><svg width="14" height="14" viewBox="0 0 14 14" fill="none" stroke="#777" stroke-width="1.3"><circle cx="7" cy="7" r="6"/><path d="M1 7h12M7 1c-3 3-3 9 0 12M7 1c3 3 3 9 0 12"/></svg></a>
      <a class="social-link" href="#" aria-label="Message"><svg width="14" height="14" viewBox="0 0 14 14" fill="none" stroke="#777" stroke-width="1.3"><path d="M1 2h12v8H5l-3 3v-3H1z"/></svg></a>
      <a class="social-link" href="#" aria-label="Email"><svg width="14" height="12" viewBox="0 0 14 12" fill="none" stroke="#777" stroke-width="1.3"><rect x="1" y="1" width="12" height="10"/><path d="M1 1l6 5 6-5"/></svg></a>
    </div>
  </section>

  <footer class="site-footer">
    <div class="copyright">© <b>BRAMBLECREST FINISHING WORKS</b> - 2018 . All Right Reserved</div>
    <div class="footer-links"><a href="#">Home</a><i>|</i><a href="#">About</a><i>|</i><a href="#">Services</a><i>|</i><a href="#">Contact</a></div>
  </footer>
</div>
</body>
</html>
```